We need our current web site completely overhauled logo and all. www.maplecrestkidsclub.com

This is a web site for a before and after school program for kids. I would like to see a fresh and cleaner version. The current version was created 8 to 10 years ago.
www.maplecrestkidsclub.com

```html
<!DOCTYPE html>
<html lang="en">
<head>
<meta charset="utf-8">
<title>Maplecrest Kids Club – Before &amp; After School Program</title>
<link href="https://fonts.googleapis.com/css2?family=PT+Sans+Narrow:wght@400;700&family=Ubuntu:wght@300;400;500&display=swap" rel="stylesheet">
<style>
:root{
  --green:#0b5a2a;
  --green-dark:#063d1c;
  --green-light:#0e6b33;
  --yellow:#f3c623;
  --grey-bg:#ebebeb;
  --text:#666;
  --footer:#232323;
  --white:#fff;
}
*{margin:0;padding:0;box-sizing:border-box}
html,body{width:846px;height:1200px;overflow:hidden;background:var(--white)}
body{position:relative;font-family:"Ubuntu",sans-serif;color:var(--text)}
.abs{position:absolute}
.heading{font-family:"PT Sans Narrow",sans-serif;font-weight:700;color:var(--green);font-size:17px;letter-spacing:.1px}

/* header */
.top-band{left:0;top:0;width:846px;height:500px}
.brand{left:60px;top:26px;font-family:"Ubuntu",sans-serif;font-weight:500;font-size:20px;line-height:21px;color:var(--green);display:flex;align-items:center;gap:6px}
.brand-dot{width:14px;height:14px;border-radius:50%;background:var(--green)}
.tagline{left:205px;top:50px;font-size:10.5px;font-weight:300;color:#444;white-space:nowrap}
.search{left:623px;top:47px;width:160px;height:20px;background:var(--white);border:1px solid #ddd;font-size:9px;color:#aaa;padding:5px 7px}
.search svg{position:absolute;right:5px;top:5px}

.nav{left:62px;top:79px;width:723px;height:51px;background:var(--green);border-radius:3px 3px 0 0}
.nav a{position:absolute;top:17px;font-family:"PT Sans Narrow",sans-serif;font-weight:700;font-size:14.5px;color:var(--white);text-decoration:none}
.nav .more{left:656px;top:14px;width:56px;height:22px;background:#111;border-radius:2px;font-size:11px;padding:4px 8px}

.hero{left:62px;top:130px;width:723px;height:316px;background:linear-gradient(120deg,#c43a2f 0%,#8b6a4d 35%,#b06c7a 55%,#5e7c8e 75%,#4b6d3f 100%)}
.hero-word{left:86px;top:328px;font-family:"Ubuntu",sans-serif;font-weight:300;font-size:40px;color:var(--white)}

/* welcome */
.welcome-title{left:62px;top:522px}
.welcome-frame{left:62px;top:557px;width:292px;height:172px;background:var(--white);border:1px solid #ddd;box-shadow:0 1px 3px rgba(0,0,0,.2)}
.welcome-photo{position:absolute;left:6px;top:6px;width:279px;height:159px;background:linear-gradient(135deg,#c9b48e 0%,#6f8f4e 40%,#2f5a48 70%,#d7c7a8 100%)}
.welcome-text{left:363px;top:572px;width:423px;font-size:9.2px;font-weight:300;line-height:18.4px;text-align:justify}
.welcome-text b{font-weight:500;color:#333}

/* lower */
.lower{left:0;top:768px;width:846px;height:358px;background:var(--grey-bg)}
.kids-title{left:62px;top:784px}
.poster{width:62px;height:84px;border:1px solid #ccc}
.fee-title{left:308px;top:784px}
.fee-name{left:308px;top:836px;display:flex;align-items:center;gap:7px;font-family:"Ubuntu",sans-serif;font-weight:400;font-size:14px;color:#444}
.fee-square{width:12px;height:12px;background:var(--green)}
.how{left:308px;top:903px;font-size:10.5px;color:var(--green)}
.steps{left:308px;top:921px;width:232px;font-size:9.2px;line-height:18.4px;color:#444;list-style:none}

.side{left:554px;top:748px;width:231px;height:398px;background:linear-gradient(180deg,#0c5a2b 0%,#063d1c 100%)}
.side-title{position:absolute;left:44px;font-family:"PT Sans Narrow",sans-serif;font-weight:700;font-size:16.5px;color:var(--white)}
.side-icon{position:absolute;left:12px}
.side p{position:absolute;left:15px;width:196px;font-size:9.2px;line-height:18.4px;color:#eee;text-align:justify}
.side .sub{color:var(--yellow);font-weight:500}
.side .rule{position:absolute;left:0;width:231px;height:1px;background:rgba(255,255,255,.12)}
.field{position:absolute;left:16px;width:196px;height:19px;background:#052f15;border:1px solid #2a6a40;font-size:7.5px;color:#6a8a75;padding:4px 6px}
.submit{position:absolute;left:16px;top:344px;width:51px;height:17px;background:var(--green-light);color:var(--white);font-family:"PT Sans Narrow",sans-serif;font-weight:700;font-size:10px;text-align:center;line-height:17px;border-radius:2px}

/* footer */
.footer{left:0;top:1126px;width:846px;height:74px;background:var(--footer)}
.foot-links{position:absolute;left:69px;top:20px;font-size:9.5px;color:#ddd;word-spacing:2px}
.foot-links span{color:#888;margin:0 9px}
.copy{position:absolute;left:69px;top:46px;font-size:9.5px;color:#ddd}
.social{position:absolute;top:37px;width:18px;height:18px;border-radius:50%}
</style>
</head>
<body>

<svg class="abs top-band" width="846" height="500" viewBox="0 0 846 500" aria-hidden="true">
  <defs>
    <radialGradient id="curveShade" cx="0.5" cy="0" r="0.6">
      <stop offset="0" stop-color="#dcdcdc"/><stop offset="1" stop-color="#efefef"/>
    </radialGradient>
  </defs>
  <rect width="846" height="440" fill="#ebebeb"/>
  <path d="M0 440 Q423 530 846 440 L846 500 L0 500Z" fill="#fff"/>
  <path d="M0 440 Q423 530 846 440 Q423 475 0 440Z" fill="url(#curveShade)"/>
</svg>

<div class="abs brand"><span class="brand-dot"></span>Maplecrest<br>Kids Club</div>
<div class="abs tagline">Maplecrest - Montessori Schools - Brookfield &nbsp;Sports • Recreation • Homework Club</div>
<div class="abs search">Search
  <svg width="10" height="10" viewBox="0 0 10 10"><circle cx="4" cy="4" r="3" fill="none" stroke="#999" stroke-width="1.2"/><line x1="6.2" y1="6.2" x2="9" y2="9" stroke="#999" stroke-width="1.4"/></svg>
</div>

<nav class="abs nav">
  <a style="left:23px">HOME</a>
  <a style="left:87px">PROGRAMS</a>
  <a style="left:181px">MAPLECREST</a>
  <a style="left:288px">CONTACT</a>
  <a style="left:370px">LOCATIONS</a>
  <a style="left:465px">FEE EXPRESS</a>
  <a class="more">MORE &nbsp;▼</a>
</nav>

<div class="abs hero" role="img" aria-label="Photo of three smiling children climbing playground bars outdoors"></div>
<div class="abs hero-word">Adventure</div>

<svg class="abs" style="left:384px;top:463px" width="66" height="14" aria-hidden="true">
  <circle cx="7" cy="7" r="6.5" fill="#063d1c"/>
  <circle cx="24" cy="7" r="6.5" fill="#bbb"/>
  <circle cx="41" cy="7" r="6.5" fill="#bbb"/>
  <circle cx="58" cy="7" r="6.5" fill="#bbb"/>
</svg>

<h2 class="abs heading welcome-title">WELCOME TO MAPLECREST KIDS CLUB</h2>
<div class="abs welcome-frame"><div class="welcome-photo" role="img" aria-label="Photo of smiling schoolchildren in a classroom, one holding a molecule model"></div></div>
<p class="abs welcome-text">The Maplecrest Before and After School Program exists to provide programming of the highest quality for your children, stressing a safe, secure environment; a nurturing, professional staff and lots of fun. We are committed to providing a fun-filled, rewarding program that supports the physical, mental, emotional and spiritual development of school-age children and their families to the fullest potential in order to improve their quality of life.<br>For parents, our goal is to provide as much parental convenience as possible. It is our desire that when the work day is finished, a parent's evening focuses on nurturing their family, To help make this possible, we offer optional conveniences such .... <b>Read More</b></p>

<div class="abs lower"></div>

<h2 class="abs heading kids-title">KIDS PLACE</h2>
<div class="abs poster" style="left:68px;top:821px;background:linear-gradient(#c4301c,#2a2a2a)" role="img" aria-label="Movie poster"></div>
<div class="abs poster" style="left:139px;top:821px;background:linear-gradient(#3a3d8a,#6b4a8f)" role="img" aria-label="Movie poster"></div>
<div class="abs poster" style="left:208px;top:821px;background:linear-gradient(#e8e8e8,#c0272d)" role="img" aria-label="Movie poster"></div>
<div class="abs poster" style="left:68px;top:914px;background:linear-gradient(#1d6fb8,#0c3d6b)" role="img" aria-label="Movie poster"></div>
<div class="abs poster" style="left:139px;top:914px;background:linear-gradient(#2b5aa8,#e0a02a)" role="img" aria-label="Movie poster"></div>
<div class="abs poster" style="left:208px;top:914px;background:linear-gradient(#d6341f,#f0e6d8)" role="img" aria-label="Movie poster"></div>
<div class="abs poster" style="left:68px;top:1012px;background:linear-gradient(#3c7bb5,#4a6a3a)" role="img" aria-label="Movie poster"></div>
<div class="abs poster" style="left:139px;top:1012px;background:linear-gradient(#4a9ad8,#2a5a9a)" role="img" aria-label="Movie poster"></div>
<div class="abs poster" style="left:208px;top:1012px;background:linear-gradient(#f0d88a,#9a5aa0)" role="img" aria-label="Movie poster"></div>

<h2 class="abs heading fee-title">FEE EXPRESS</h2>
<div class="abs fee-name"><span class="fee-square"></span>Fee Express</div>
<div class="abs how">How it will work:</div>
<ul class="abs steps">
  <li>• Parents will complete a Parent Authorization Form allowing Maplecrest to automatically debit your account (or credit card).</li>
  <li>• Your due date will not change. Payments are taken every MONDAY!</li>
  <li>• You can also receive instant e-mail notifications by signing up at:<br>www.feeexpresspay.com</li>
  <li>• There are no long term commitments required.</li>
</ul>

<svg class="abs" style="left:544px;top:748px" width="251" height="398" aria-hidden="true">
  <polygon points="0,20 10,0 10,20" fill="#111"/>
  <polygon points="241,0 251,20 241,20" fill="#111"/>
  <polygon points="0,378 10,378 10,398" fill="#111"/>
  <polygon points="241,378 251,378 241,398" fill="#111"/>
</svg>
<aside class="abs side">
  <div class="rule" style="top:30px"></div>
  <svg class="side-icon" style="top:34px" width="24" height="20" viewBox="0 0 24 20" aria-hidden="true">
    <path d="M2 7h5l9-6v18l-9-6H2z" fill="#fff"/><rect x="4" y="13" width="3" height="6" fill="#fff"/><line x1="19" y1="10" x2="23" y2="10" stroke="#fff" stroke-width="2"/>
  </svg>
  <div class="side-title" style="top:34px">PROGRAMS</div>
  <p style="top:77px"><span class="sub">Maplecrest Before &amp; After School Program</span><br>The Maplecrest at the Oakridge Community Rec Center provides before &amp; after school programming of the highest quality, stressing a safe, secure environment .</p>
  <p style="top:176px">Registration Forms, Photos &amp; More &gt;&gt;</p>
  <div class="rule" style="top:210px"></div>
  <svg class="side-icon" style="top:227px" width="24" height="16" viewBox="0 0 24 16" aria-hidden="true">
    <rect x="1" y="1" width="22" height="14" fill="none" stroke="#fff" stroke-width="1.6"/><path d="M1 1l11 8 11-8M1 15l8-7M23 15l-8-7" fill="none" stroke="#fff" stroke-width="1.4"/>
  </svg>
  <div class="side-title" style="top:222px">SUBSCRIBE NEWSLETTER</div>
  <p style="top:246px">Lorem Ipsum is simply dummy text of the printing and typesetting industry.</p>
  <div class="field" style="top:288px">Enter the name</div>
  <div class="field" style="top:315px">Enter the E-Mail ID</div>
  <div class="submit">SUBMIT</div>
</aside>

<footer class="abs footer">
  <div class="foot-links">Home<span>|</span>Programs<span>|</span>Maplecrest<span>|</span>Contact<span>|</span>Locations<span>|</span>Fee Express &nbsp;▼</div>
  <div class="copy">Copyright ©2013 Maplecrest Kids Club &nbsp;&nbsp;- All rights reserved</div>
  <div class="social" style="left:686px;background:#4aa3df"></div>
  <div class="social" style="left:706px;background:#3b5998"></div>
  <div class="social" style="left:726px;background:#d9483b"></div>
  <div class="social" style="left:746px;background:#1b75bb"></div>
  <div class="social" style="left:767px;background:#f39c1f"></div>
</footer>

</body>
</html>
```